Web Design

We need a website for a company based in Doha Qatar called
Lumara Maid Service.

It is the number one maid cleaning service company, and we have branches all over qatar.

Luxury Cleaning Service Provider.

The color scheme is gold, yellow and black like the logo.

Before they get to the website, there is an intro video.

The website should depict luxury.

Target Market(s)

People who need maids at their houses.

Industry/Entity Type

Cleaning Service

Requirements
Must have
• Luxury, Sleek, Modern

The opening sequence is a video which I already have. Its too big to upload here so I am going to put it on youtube.

After the opening sequence, the home page should have a widescreen photo background and it should change every five seconds, the first background photo should be of qatar westbay skyline. Then the second background should be of maid photos in cleaning positions. Then the third background should be of cleaner photos etc.

We will send you all the tabs and all the content later.

```html
<!DOCTYPE html>
<html lang="en">
<head>
<meta charset="utf-8">
<title>Lumara Maid Service – Videos</title>
<link rel="stylesheet" href="https://fonts.googleapis.com/css2?family=Questrial&family=Roboto+Condensed:wght@400&display=swap">
<style>
  :root {
    --bg-dark: #1b1b1b;
    --nav-grey: #9a9a9a;
    --gold: #f0c75a;
    --white: #ffffff;
    --footer-text: #c9c9c9;
    --bar-dark: #141414;
    --track: #3a3a3a;
    --lime: #b6e04a;
    --side-btn: #5c5c5c;
  }
  * { margin: 0; padding: 0; box-sizing: border-box; }
  html, body { width: 1200px; height: 851px; overflow: hidden; background: var(--bg-dark); }
  body { position: relative; font-family: "Questrial", sans-serif; }

  .site-header { position: absolute; left: 0; top: 0; width: 1200px; height: 112px; background: var(--bg-dark); }
  .brand { position: absolute; left: 82px; top: 38px; display: flex; align-items: center; gap: 10px;
           color: var(--gold); font-size: 20px; letter-spacing: .5px; }
  .brand-dot { width: 22px; height: 22px; border-radius: 50%; background: var(--gold); }
  .main-nav a { position: absolute; top: 45px; transform: translateX(-50%); color: var(--nav-grey);
                text-decoration: none; font-size: 16px; white-space: nowrap; }
  .main-nav a.active { color: var(--gold); }

  .video-stage { position: absolute; left: 0; top: 112px; width: 1200px; height: 661px; overflow: hidden; }
  .video-poster { position: absolute; inset: 0;
    background:
      radial-gradient(ellipse 260px 330px at 640px 280px, rgba(60,110,170,.85), transparent 70%),
      radial-gradient(ellipse 330px 420px at 320px 360px, rgba(200,170,20,.9), transparent 70%),
      radial-gradient(ellipse 220px 300px at 950px 420px, rgba(110,95,20,.7), transparent 70%),
      linear-gradient(180deg, #3c3f44 0%, #2b2e31 55%, #413b30 100%); }
  .video-shade { position: absolute; inset: 0; background: rgba(0,0,0,.28); }

  .play-big { position: absolute; left: 551px; top: 268px; }
  .video-title { position: absolute; left: 0; width: 1200px; top: 383px; text-align: center;
    font-family: "Roboto Condensed", sans-serif; font-size: 100px; color: var(--white); letter-spacing: 1px; line-height: 1; }

  .side-tools { position: absolute; right: 4px; top: 0; display: flex; flex-direction: column; gap: 5px; }
  .side-tools span { width: 33px; height: 33px; background: var(--side-btn); border-radius: 2px;
                     display: flex; align-items: center; justify-content: center; }

  .player-bar { position: absolute; left: 23px; top: 602px; width: 1156px; height: 46px; }
  .player-play { position: absolute; left: 0; top: 0; width: 75px; height: 46px; background: var(--bar-dark);
                 display: flex; align-items: center; justify-content: center; }
  .player-track-wrap { position: absolute; left: 82px; top: 9px; width: 1074px; height: 37px; background: rgba(20,20,20,.9); }
  .player-track { position: absolute; left: 13px; top: 13px; width: 883px; height: 12px; border: 1px solid var(--track); }
  .player-time { position: absolute; left: 73px; top: 0; width: 45px; height: 18px; background: #f2f2f2;
                 color: #111; font-size: 12px; text-align: center; line-height: 18px; font-family: "Roboto Condensed", sans-serif; }
  .player-tools { position: absolute; left: 905px; top: 8px; display: flex; align-items: center; gap: 9px; }
  .player-host { color: var(--white); font-size: 17px; }
  .hd { color: #777; font-family: "Roboto Condensed", sans-serif; font-size: 18px; font-style: normal; }

  .site-footer { position: absolute; left: 0; top: 773px; width: 1200px; height: 78px; background: var(--bg-dark); }
  .copyright { position: absolute; left: 33px; top: 33px; font-size: 12px; color: var(--footer-text); }
  .social { position: absolute; left: 981px; top: 24px; display: flex; gap: 7px; }
  .social span { width: 32px; height: 32px; border-radius: 50%; border: 2px solid #6a6a6a; }
</style>
</head>
<body>
  <header class="site-header">
    <div class="brand"><span class="brand-dot"></span>Lumara Maid Service</div>
    <nav class="main-nav">
      <a href="#" style="left:429px">Home</a>
      <a href="#" style="left:556px">About Us</a>
      <a href="#" style="left:690px">Services</a>
      <a href="#" style="left:807px">Blog</a>
      <a href="#" class="active" style="left:924px">Videos</a>
      <a href="#" style="left:1061px">Contact US</a>
    </nav>
  </header>

  <section class="video-stage">
    <div class="video-poster" role="img" aria-label="Video still of gloved hands cleaning a window with a spray bottle and blue cloth"></div>
    <div class="video-shade"></div>

    <div class="side-tools">
      <span><svg width="20" height="18" viewBox="0 0 20 18"><path d="M10 17 L2 9 A4.5 4.5 0 0 1 10 3 A4.5 4.5 0 0 1 18 9 Z" fill="#fff"/></svg></span>
      <span><svg width="22" height="22" viewBox="0 0 22 22"><circle cx="11" cy="11" r="9" fill="none" stroke="#fff" stroke-width="2"/><path d="M11 5 V11 L8 14" stroke="#fff" stroke-width="2" fill="none"/></svg></span>
      <span><svg width="20" height="20" viewBox="0 0 20 20"><path d="M1 9 L19 1 L13 19 L10 11 Z" fill="#fff"/></svg></span>
    </div>

    <svg class="play-big" width="98" height="98" viewBox="0 0 98 98">
      <circle cx="49" cy="49" r="47" fill="#555" stroke="#888" stroke-width="3"/>
      <path d="M36 27 L75 49 L36 71 Z" fill="#9bd23a"/>
    </svg>

    <h1 class="video-title">LUMARA MAID SERVICE</h1>

    <div class="player-bar">
      <div class="player-play"><svg width="22" height="24" viewBox="0 0 22 24"><path d="M0 0 L22 12 L0 24 Z" fill="#fff"/></svg></div>
      <div class="player-track-wrap">
        <div class="player-track"></div>
        <div class="player-tools">
          <svg width="28" height="16" viewBox="0 0 28 16"><g fill="#b6e04a"><rect x="0" y="0" width="3" height="16"/><rect x="6" y="0" width="3" height="16"/><rect x="12" y="0" width="3" height="16"/><rect x="18" y="0" width="3" height="16"/><rect x="24" y="0" width="3" height="16"/></g></svg>
          <span class="hd">HD</span>
          <svg width="14" height="14" viewBox="0 0 14 14"><path d="M0 0 L5 0 L0 5 Z M14 0 L14 5 L9 0 Z M0 14 L0 9 L5 14 Z M14 14 L9 14 L14 9 Z" fill="#fff"/></svg>
          <span class="player-host">ClipHost</span>
        </div>
      </div>
      <div class="player-time">04:21</div>
    </div>
  </section>

  <footer class="site-footer">
    <p class="copyright">Copy Rights 2014 Lumara Maid Service. All Rights Reserved.</p>
    <div class="social"><span></span><span></span><span></span><span></span></div>
  </footer>
</body>
</html>
```